TALMORK

The business want a professional looking business card. We have a scetch we will add but want the extra upgrade, and would like more suggestions for variations of our business cards.

```html
<!DOCTYPE html>
<html lang="en">
<head>
<meta charset="utf-8">
<title>TALMORK — Business Card</title>
<link rel="stylesheet" href="https://fonts.googleapis.com/css2?family=Marcellus&family=Jost:wght@400;500&display=swap">
<style>
  :root {
    --backdrop: #d9d3ca;
    --card: #f3efe5;
    --card-edge: #e6e0d2;
    --ink: #3f2c20;
    --ink-soft: #4d3b2f;
    --gold: #b8904f;
    --gold-light: #d8bd86;
    --grid-line: #cdbfa6;
    --ornament-a: #e9e2d2;
    --ornament-b: #ddd2bc;
  }
  * { box-sizing: border-box; margin: 0; padding: 0; }
  html, body { width: 1200px; height: 805px; overflow: hidden; }
  body {
    background: var(--backdrop);
    position: relative;
    font-family: "Jost", Arial, sans-serif;
  }
  .card {
    position: absolute;
    top: 244px;
    width: 480px;
    height: 316px;
    background: var(--card);
    box-shadow: 0 10px 24px rgba(60, 40, 20, 0.18);
    overflow: hidden;
  }
  .card--front { left: 94px; }
  .card--back { left: 626px; }

  /* Front */
  .holder-name {
    position: absolute; left: 35px; top: 38px;
    font-family: "Marcellus", Georgia, serif;
    font-size: 31px; color: var(--ink); letter-spacing: 0.2px;
  }
  .holder-role {
    position: absolute; left: 35px; top: 84px;
    font-size: 19px; color: var(--ink-soft);
  }
  .contact-list {
    position: absolute; left: 35px; top: 210px;
    list-style: none;
  }
  .contact-item {
    display: flex; align-items: center; gap: 9px;
    height: 27px;
    font-size: 16.5px; color: var(--ink-soft);
  }
  .contact-icon { width: 18px; height: 18px; flex: none; }
  .front-ornament {
    position: absolute; right: 0; top: 0;
    width: 180px; height: 316px;
    background: radial-gradient(ellipse at 85% 55%, var(--ornament-b) 0%, var(--ornament-a) 45%, var(--card) 75%);
  }

  /* Back */
  .layout-grid { position: absolute; inset: 0; }
  .gold-rule {
    position: absolute; left: 378px; top: 20px;
    width: 3px; height: 292px; background: var(--gold);
  }
  .brand-dot {
    position: absolute; left: 167px; top: 86px;
    width: 66px; height: 66px; border-radius: 50%;
    background: linear-gradient(160deg, var(--gold-light), var(--gold));
  }
  .brand-name {
    position: absolute; left: 0; width: 400px; top: 184px;
    text-align: center;
    font-family: "Marcellus", Georgia, serif;
    font-size: 36px; letter-spacing: 1.5px; color: var(--ink);
  }
  .brand-since {
    position: absolute; left: 0; width: 400px; top: 231px;
    text-align: center;
    font-size: 11px; letter-spacing: 3px; color: var(--ink-soft);
  }
</style>
</head>
<body>

<section class="card card--front">
  <div class="front-ornament" role="img" aria-label="Large embossed floral brand ornament"></div>
  <h1 class="holder-name">Halvard Eirik Lundmo</h1>
  <p class="holder-role">CEO &amp; Founder</p>
  <ul class="contact-list">
    <li class="contact-item">
      <svg class="contact-icon" viewBox="0 0 18 18" fill="none" stroke="#4d3b2f" stroke-width="1.4"><rect x="5" y="1.5" width="8" height="15" rx="1.6"/><line x1="8" y1="14" x2="10" y2="14"/></svg>
      004791234567
    </li>
    <li class="contact-item">
      <svg class="contact-icon" viewBox="0 0 18 18" fill="none" stroke="#4d3b2f" stroke-width="1.4"><rect x="1.5" y="4" width="15" height="10.5" rx="1"/><polyline points="1.5,4.5 9,10 16.5,4.5"/></svg>
      post@talmork.llc
    </li>
    <li class="contact-item">
      <svg class="contact-icon" viewBox="0 0 18 18" fill="none" stroke="#4d3b2f" stroke-width="1.3"><circle cx="9" cy="9" r="7.3"/><ellipse cx="9" cy="9" rx="3.2" ry="7.3"/><line x1="1.7" y1="9" x2="16.3" y2="9"/></svg>
      www.talmork.llc
    </li>
  </ul>
</section>

<section class="card card--back">
  <svg class="layout-grid" width="480" height="316" viewBox="0 0 480 316" stroke="#cdbfa6" stroke-width="1">
    <line x1="90" y1="0" x2="90" y2="316"/>
    <line x1="290" y1="0" x2="290" y2="316"/>
    <line x1="0" y1="75" x2="380" y2="75"/>
    <line x1="0" y1="192" x2="380" y2="192"/>
    <line x1="0" y1="217" x2="380" y2="217"/>
    <line x1="0" y1="236" x2="380" y2="236"/>
  </svg>
  <div class="brand-dot"></div>
  <p class="brand-name">TALMORK</p>
  <p class="brand-since">SINCE 2026</p>
  <div class="gold-rule"></div>
</section>

</body>
</html>
```